Brivolt Technologies business card design

We need a business card designed with our new logo. it would be great if the card could communicate it is a technology based company.

Target Market(s)

system integrators

Industry/Entity Type

technology, IOT

Contact Information for Business Card

Name, designation, Address, telephone number, email address

Requirements
Must have
• logo and company name
Nice to have
• something to do with technology

```html
<!DOCTYPE html>
<html lang="en">
<head>
<meta charset="utf-8">
<title>Brivolt Technologies – Business Card</title>
<link rel="stylesheet" href="https://fonts.googleapis.com/css2?family=Michroma&family=Questrial&display=swap">
<style>
  :root {
    --backdrop: #8c8c8c;
    --brand-orange: #f5951f;
    --brand-orange-pale: #fbd3a3;
    --ink-dark: #3a3a3c;
    --paper: #ffffff;
    --card-shadow: 0 18px 30px rgba(0, 0, 0, 0.28);
  }
  * { box-sizing: border-box; margin: 0; padding: 0; }
  html, body {
    width: 1200px;
    height: 800px;
    overflow: hidden;
    background: var(--backdrop);
  }
  .canvas {
    width: 1200px;
    height: 800px;
    display: flex;
    align-items: center;
    justify-content: center;
    gap: 50px;
  }
  .card {
    position: relative;
    width: 530px;
    height: 310px;
    border-radius: 24px;
    overflow: hidden;
    box-shadow: var(--card-shadow);
  }

  /* Front: orange contact side */
  .card--front { background: var(--brand-orange); color: var(--paper); }
  .card__decoration {
    position: absolute;
    left: 0;
    bottom: 0;
    width: 330px;
    height: 230px;
    background: linear-gradient(200deg, var(--brand-orange-pale) 0%, var(--paper) 55%);
    clip-path: polygon(0 40%, 55% 0, 100% 45%, 72% 100%, 0 100%);
  }
  .contact {
    position: absolute;
    top: 42px;
    right: 34px;
    text-align: right;
  }
  .contact__name {
    font-family: "Michroma", sans-serif;
    font-weight: 400;
    font-size: 27px;
    letter-spacing: 1px;
    line-height: 1.1;
  }
  .contact__title {
    font-family: "Questrial", sans-serif;
    font-size: 17px;
    margin-top: 4px;
  }
  .contact__list {
    list-style: none;
    margin-top: 22px;
    font-family: "Questrial", sans-serif;
    font-size: 15px;
    line-height: 1.7;
  }
  .contact__item {
    display: flex;
    align-items: center;
    justify-content: flex-end;
    gap: 10px;
  }
  .contact__icon { width: 12px; height: 12px; flex: none; }

  /* Back: white name side */
  .card--back {
    background: var(--paper);
    display: flex;
    align-items: center;
    justify-content: center;
  }
  .brand {
    display: flex;
    align-items: center;
    gap: 18px;
  }
  .brand__square {
    width: 40px;
    height: 40px;
    background: var(--brand-orange);
    flex: none;
  }
  .brand__name {
    font-family: "Michroma", sans-serif;
    font-size: 30px;
    line-height: 1.25;
    color: var(--ink-dark);
    letter-spacing: 1px;
  }
</style>
</head>
<body>
<main class="canvas">
  <section class="card card--front">
    <div class="card__decoration" role="img" aria-label="Enlarged brand symbol decoration in white and orange blocks"></div>
    <div class="contact">
      <h1 class="contact__name">DANIEL REYES</h1>
      <p class="contact__title">Founder &amp; CEO</p>
      <ul class="contact__list">
        <li class="contact__item">(555) 010-2468
          <svg class="contact__icon" viewBox="0 0 12 12" aria-hidden="true"><path d="M3 1 L5 3.5 L3.8 5 Q5 7.5 7 8.2 L8.5 7 L11 9 L9.5 11 Q4.5 10.5 1 3 Z" fill="#fff"/></svg>
        </li>
        <li class="contact__item">daniel@brivolttech.com
          <svg class="contact__icon" viewBox="0 0 12 12" aria-hidden="true"><rect x="0.5" y="2.5" width="11" height="7.5" fill="#fff"/><path d="M0.5 2.5 L6 7 L11.5 2.5" fill="none" stroke="#f5951f" stroke-width="1"/></svg>
        </li>
        <li class="contact__item">brivolttech.com
          <svg class="contact__icon" viewBox="0 0 12 12" aria-hidden="true"><circle cx="6" cy="6" r="5.5" fill="#fff"/><path d="M0.5 6 H11.5 M6 0.5 Q3 6 6 11.5 M6 0.5 Q9 6 6 11.5" fill="none" stroke="#f5951f" stroke-width="0.8"/></svg>
        </li>
      </ul>
    </div>
  </section>

  <section class="card card--back">
    <div class="brand">
      <span class="brand__square" aria-hidden="true"></span>
      <span class="brand__name">BRIVOLT<br>TECHNOLOGIES</span>
    </div>
  </section>
</main>
</body>
</html>
```